ecommerce news podcast artwork

Podcast cover art for a podcast featuring daily news and events around ecommerce product businesses.

text to be: BRISK LOOP
optional third line of text with smaller font: Podcast

looking for something that pops with a medium to light blue background. text can be in white/red/orange colors. prefer solid colors for text, but background can vary.
I'm really open to other ideas too, sometimes you don't know what you want until you see it.

Target Market(s)

ecommerce business owners, managers

Industry/Entity Type

news, business, ecommerce

Font styles to use
Sans Serif

Colors
0054AA
0677BA
7BADD7
CADEEF
E8F1F8
0094D4
00A9DD
6FCCEA
C7EBF8
E9F6FB
F0912C
F2A743
F7CA91
FBE8D2
FDF5EE
EB3D1F
EC4F4E
F09395
F8D3D4
FCEDEE

Requirements
Must have
• text: BRISK LOOP
Should not have
• no microphones, headsets/headphones, speakers, or other props like that.

```html
<!DOCTYPE html>
<html lang="en">
<head>
<meta charset="utf-8">
<title>Brisk Loop Podcast Cover</title>
<link rel="stylesheet" href="https://fonts.googleapis.com/css2?family=Montserrat:wght@400;700&display=swap">
<style>
  :root {
    --page: #dcd9da;
    --sky-light: #a8eded;
    --sky-mid: #7fd4dc;
    --sky-deep: #50b0bf;
    --ink: #242424;
    --orange: #ff7f00;
  }
  html, body {
    margin: 0;
    padding: 0;
    width: 1200px;
    height: 1121px;
    overflow: hidden;
    background: var(--page);
  }
  .canvas {
    display: block;
    width: 1200px;
    height: 1121px;
  }
  .title {
    font-family: "Montserrat", sans-serif;
    font-weight: 700;
  }
  .title-top { fill: var(--ink); font-size: 200px; }
  .title-bottom { fill: var(--orange); font-size: 228px; }
  .subtitle {
    font-family: "Montserrat", sans-serif;
    font-weight: 400;
    font-size: 28px;
    fill: var(--ink);
  }
  .frame { fill: none; stroke: var(--ink); stroke-width: 2.6; }
</style>
</head>
<body>
<svg class="canvas" viewBox="0 0 1200 1121" xmlns="http://www.w3.org/2000/svg">
  <defs>
    <radialGradient id="cover-glow" cx="600" cy="520" r="560" gradientUnits="userSpaceOnUse">
      <stop offset="0" stop-color="var(--sky-light)"/>
      <stop offset="0.55" stop-color="var(--sky-mid)"/>
      <stop offset="1" stop-color="var(--sky-deep)"/>
    </radialGradient>
  </defs>

  <g class="cover">
    <rect class="cover-bg" x="168" y="128" width="864" height="864" fill="url(#cover-glow)"/>
    <rect class="frame" x="206" y="165" width="792" height="792"/>

    <text class="title title-top" x="242" y="500" textLength="710" lengthAdjust="spacing">BRISK</text>
    <text class="title title-bottom" x="248" y="740" textLength="710" lengthAdjust="spacing">LOOP</text>
    <text class="subtitle" x="502" y="810" textLength="199" lengthAdjust="spacing">PODCAST</text>
  </g>
</svg>
</body>
</html>
```